Calder Vane LED - E- Commerce site

We need a website designed for an LED Billboard company that sells:
1) LED Billboards (Sales & Rental)
2) LED Gas Station lights
3) Truss Systems (Sales & Rental)
4) Sound Systems (Sales & Rental)

Attached are websites that sell similar products as Calder Vane LED. Target market is for business, property managers and event coordinators.
This site will need to be an e-commerce site where customers can purchase the product directly from the site. What I'm looking for is a design layout to start.

Conceptual Web Designs:
http://192.0.2.47:8087/index.html
http://www.pmvdisplay.example/
http://www.auralomaaudio.example/
http://www.quillmarkpanel.example/

Attached is the logo of the company: Please note that the new spelling of the logo is "Calder Vane LED" using domain " CalderVaneLED.com

Industry/Entity Type

Gas Station

Number of Pages Required

5+ page

Requirements
Must have
• 1) E-Commerce - Customers will need to be able to order product from the site.
• 2) Customers will also have the option to rent the product as well.
Nice to have
• I like the image of the attached website, that has a video clip loop
• http://www.quillmarkpanel.example/

```html
<!DOCTYPE html>
<html lang="en">
<head>
<meta charset="utf-8">
<title>Calder Vane LED</title>
<link href="https://fonts.googleapis.com/css2?family=Rajdhani:wght@500;600;700&family=Lato:wght@400;700&display=swap" rel="stylesheet">
<style>
:root{
  --yellow:#f6c31c;
  --dark:#1b1b1b;
  --footer:#232323;
  --pink:#e0146c;
  --red:#e3302f;
  --teal:#1e9c86;
  --teal-deep:#127564;
  --grey-bg:#ececec;
  --text:#2a2a2a;
  --muted:#555;
  --white:#fff;
}
*{box-sizing:border-box;margin:0;padding:0}
html,body{width:1200px;height:2941px;overflow:hidden}
body{position:relative;font-family:'Lato',sans-serif;color:var(--text);background:var(--white)}
.abs{position:absolute}
.display{font-family:'Rajdhani',sans-serif}

/* utility bar */
.utility-bar{left:0;top:0;width:1200px;height:43px;background:var(--yellow)}
.utility-link{position:absolute;top:8px;display:flex;align-items:center;gap:10px;font-size:13px;font-weight:700;color:#1d1d1d}
.utility-icon{width:26px;height:26px;border-radius:50%;background:var(--teal);display:flex;align-items:center;justify-content:center}
.search-box{position:absolute;right:98px;top:0;width:43px;height:43px;background:#e2a90c;display:flex;align-items:center;justify-content:center}

/* nav */
.main-nav{left:0;top:43px;width:1200px;height:98px;background:var(--dark);border-bottom:2px solid #444}
.brand{position:absolute;left:98px;top:24px;display:flex;align-items:center;gap:12px;font-family:'Rajdhani',sans-serif;font-weight:700;font-size:30px;color:var(--yellow);line-height:1}
.brand-dot{width:40px;height:40px;border-radius:50%;background:var(--yellow)}
.menu{position:absolute;right:98px;top:37px;display:flex;font-family:'Rajdhani',sans-serif;font-weight:600;font-size:18px;color:var(--white)}
.menu span{padding:0 17px;border-left:1px solid #444;line-height:22px}
.menu span:first-child{border-left:none;color:var(--yellow)}
.menu span:last-child{padding-right:0}

/* hero */
.hero{left:0;top:141px;width:1200px;height:512px;background:linear-gradient(180deg,#2c2a30 0%,#4a3a44 40%,#302b2f 75%,#1c1a1c 100%)}
.hero-sub{right:98px;top:150px;font-family:'Rajdhani',sans-serif;font-weight:500;font-size:36px;color:var(--white)}
.hero-title{right:98px;top:200px;font-family:'Rajdhani',sans-serif;font-weight:600;font-size:68px;color:var(--white);letter-spacing:-0.5px}
.shop-btn{right:99px;top:300px;width:233px;height:59px;background:var(--white);border-radius:6px;display:flex;align-items:center;overflow:hidden}
.shop-btn span{flex:1;text-align:center;font-family:'Rajdhani',sans-serif;font-weight:700;font-size:30px;color:#111}
.shop-btn i{width:58px;height:59px;background:var(--yellow);display:flex;align-items:center;justify-content:center}
.dots{right:98px;top:388px;display:flex;gap:12px}
.dots b{width:15px;height:15px;border-radius:50%;background:var(--white)}
.dots b:first-child{background:var(--yellow)}

/* categories */
.tile{width:484px;height:186px}
.tile-frame{position:absolute;left:16px;top:8px;right:16px;bottom:8px;border:2px solid rgba(255,255,255,.9)}
.tile-label{position:absolute;left:32px;top:24px;font-family:'Rajdhani',sans-serif;font-weight:600;color:var(--white);line-height:.95}
.tile-label .l1{font-size:48px;display:block}
.tile-label .l2{font-size:34px;display:block}
.tile-arrow{position:absolute;right:10px;bottom:8px;width:50px;height:50px;border-radius:50%;background:var(--white);display:flex;align-items:center;justify-content:center;box-shadow:0 0 0 4px rgba(255,255,255,.5)}

/* section bars */
.section-bar{left:98px;width:1003px;height:45px;display:flex;align-items:center;justify-content:space-between;padding:0 18px 0 20px}
.section-bar h2{font-family:'Rajdhani',sans-serif;font-weight:600;font-size:27px;color:var(--white)}
.pager{display:flex;gap:8px}
.pager i{width:26px;height:26px;border-radius:50%;background:var(--white);display:flex;align-items:center;justify-content:center}

/* product cards */
.card{width:240px;height:300px;background:var(--white);box-shadow:0 1px 4px rgba(0,0,0,.18)}
.card-media{position:absolute;left:0;top:0;width:240px;height:172px;background:#f5f5f5;display:flex;align-items:center;justify-content:center}
.card-title{position:absolute;left:0;width:240px;top:186px;text-align:center;font-size:18px;color:#222}
.card-text{position:absolute;left:0;width:240px;top:214px;text-align:center;font-size:14px;color:#333}
.card-btns{position:absolute;left:0;width:240px;top:250px;display:flex;justify-content:center;gap:14px}
.btn{height:32px;display:flex;align-items:center;justify-content:center;font-size:13px;font-weight:700;color:var(--white);text-transform:uppercase}
.btn-pink{width:92px;background:var(--pink)}
.btn-red{width:92px;background:var(--red)}
.btn-dark{width:92px;background:#2b2b2b}
.shape{border-radius:6px}

/* hot products */
.hot{left:0;top:1544px;width:1200px;height:343px;background:linear-gradient(180deg,var(--teal-deep),var(--teal) 60%,#32a98f)}
.hot-title{left:100px;top:44px;font-family:'Rajdhani',sans-serif;font-weight:600;font-size:27px;color:var(--white)}
.hot-rule{left:98px;top:86px;width:480px;height:1px;background:rgba(255,255,255,.5)}
.hot-card{top:108px;width:484px;height:204px;background:var(--white)}
.hot-media{position:absolute;left:0;top:0;width:241px;height:204px}
.hot-body{position:absolute;left:262px;top:40px;width:205px}
.hot-body h3{font-size:18px;font-weight:400;color:#222;margin-bottom:12px}
.hot-body p{font-size:14px;line-height:21px;color:#333}

/* features */
.features{left:0;top:2328px;width:1200px;height:279px;background:linear-gradient(180deg,#141a24,#2a2a33 55%,#1e1a1a)}
.feature{top:83px;width:316px;height:151px;background:rgba(255,255,255,.9);text-align:center}
.feature-icon{position:absolute;left:128px;top:-28px;width:60px;height:60px;border-radius:50%;background:var(--white);box-shadow:0 0 0 4px rgba(255,255,255,.4);display:flex;align-items:center;justify-content:center}
.feature h3{margin-top:42px;font-family:'Rajdhani',sans-serif;font-weight:600;font-size:29px;color:#111}
.feature p{margin:6px 18px 0;font-size:14px;font-weight:700;line-height:20px;color:#222}

/* newsletter */
.newsletter{left:0;top:2607px;width:1200px;height:90px;background:#f2f2f2}
.nl-icon{left:108px;top:23px;width:46px;height:46px;border-radius:50%;background:var(--red);display:flex;align-items:center;justify-content:center}
.nl-label{left:174px;top:34px;font-size:21px;color:#222}
.nl-input{left:361px;top:24px;width:258px;height:41px;background:var(--white);border:1px solid #ccc;font-size:13px;color:#666;padding:12px 14px}
.nl-btn{left:619px;top:24px;width:124px;height:41px;background:var(--red);color:var(--white);font-size:15px;font-weight:700;display:flex;align-items:center;justify-content:center}
.follow{left:790px;top:33px;font-size:21px;color:#222;display:flex;align-items:center;gap:8px}
.social{width:31px;height:31px;border-radius:50%;border:2px solid #222}

/* footer */
.footer{left:0;top:2697px;width:1200px;height:196px;background:var(--footer)}
.f-col h4{font-size:16px;font-weight:400;color:var(--teal);margin-bottom:12px}
.f-col p,.f-col li{font-size:12px;line-height:19px;color:#ddd}
.f-col ul{list-style:none}
.f-col li::before{content:"•";color:var(--white);margin-right:8px}
.f-divider{top:24px;width:1px;height:150px;background:#444}
.contact-row{display:flex;gap:14px;align-items:flex-start;font-size:12px;color:#ddd;line-height:18px;margin-bottom:14px}
.cards{display:flex;gap:6px}
.cards b{width:32px;height:20px;border-radius:2px;background:#e9e9e9}
.cards b:nth-child(2){background:#f0b23a}
.cards b:nth-child(3){background:#f5f5f5}
.cards b:nth-child(4){background:#2f6fb7}
.cards b:nth-child(5){background:#f6c31c}
.footer-brand{left:922px;top:90px;display:flex;align-items:center;gap:10px;font-family:'Rajdhani',sans-serif;font-weight:700;font-size:26px;color:var(--yellow)}
.copyright{left:0;top:2893px;width:1200px;height:48px;background:var(--teal);color:var(--white);font-size:14px;display:flex;align-items:center;justify-content:center}
</style>
</head>
<body>

<!-- utility bar -->
<div class="abs utility-bar">
  <div class="utility-link" style="left:700px"><span class="utility-icon"><svg width="14" height="14" viewBox="0 0 24 24"><path d="M12 21 3 12a5 5 0 0 1 9-6 5 5 0 0 1 9 6z" fill="#fff"/></svg></span>Wish List</div>
  <div class="utility-link" style="left:822px"><span class="utility-icon"><svg width="14" height="14" viewBox="0 0 24 24"><rect x="5" y="11" width="14" height="10" rx="1" fill="#fff"/><path d="M8 11V7a4 4 0 0 1 8 0v4" stroke="#fff" stroke-width="2.5" fill="none"/></svg></span>Log In</div>
  <div class="utility-link" style="left:924px"><span class="utility-icon"><svg width="14" height="14" viewBox="0 0 24 24"><circle cx="12" cy="8" r="5" fill="#fff"/><path d="M3 22a9 8 0 0 1 18 0z" fill="#fff"/></svg></span>My Account</div>
  <div class="search-box"><svg width="18" height="18" viewBox="0 0 24 24"><circle cx="10" cy="10" r="6.5" stroke="#1d1d1d" stroke-width="2.5" fill="none"/><path d="M15 15l6 6" stroke="#1d1d1d" stroke-width="2.5"/></svg></div>
</div>

<!-- main nav -->
<header class="abs main-nav">
  <div class="brand"><span class="brand-dot"></span>CALDER VANE LED</div>
  <nav class="menu"><span>HOME</span><span>ABOUT US</span><span>PRODUCTS FOR SALE</span><span>PRODUCTS FOR RENTAL</span><span>CONTACT US</span></nav>
</header>

<!-- hero -->
<section class="abs hero" role="img" aria-label="Night city street lined with bright LED billboards">
  <div class="abs hero-sub">Searching for a Modern LED Light?</div>
  <div class="abs hero-title">YOU'RE IN THE RIGHT PLACE!</div>
  <div class="abs shop-btn"><span>Shop Now</span><i><svg width="34" height="30" viewBox="0 0 34 30"><path d="M2 4h6l4 16h16l4-12H10" stroke="#1d1d1d" stroke-width="3" fill="none" stroke-linejoin="round"/><circle cx="14" cy="26" r="2.5" fill="#1d1d1d"/><circle cx="26" cy="26" r="2.5" fill="#1d1d1d"/></svg></i></div>
  <div class="abs dots"><b></b><b></b><b></b></div>
</section>

<!-- categories -->
<a class="abs tile" style="left:98px;top:682px;background:linear-gradient(135deg,#d9b32a,#c49a1a 55%,#8c7a3a)" role="img" aria-label="LED billboard by a roadside">
  <span class="tile-frame"></span>
  <span class="tile-label"><span class="l1">LED</span><span class="l2">BILLBOARDS</span></span>
  <span class="tile-arrow"><svg width="20" height="24" viewBox="0 0 20 24"><path d="M5 2l10 10L5 22" stroke="#333" stroke-width="2.5" fill="none"/></svg></span>
</a>
<a class="abs tile" style="left:617px;top:682px;background:linear-gradient(135deg,#1d8b7a,#127a72 50%,#0f5f5c)" role="img" aria-label="Gas station canopy lit by LED lights">
  <span class="tile-frame"></span>
  <span class="tile-label"><span class="l1">LED</span><span class="l2">GAS STATION LIGHTS</span></span>
  <span class="tile-arrow"><svg width="20" height="24" viewBox="0 0 20 24"><path d="M5 2l10 10L5 22" stroke="#333" stroke-width="2.5" fill="none"/></svg></span>
</a>
<a class="abs tile" style="left:98px;top:896px;background:linear-gradient(135deg,#b0198f,#8c1480 55%,#5d1463)" role="img" aria-label="Stage truss rig under purple lights">
  <span class="tile-frame"></span>
  <span class="tile-label"><span class="l1">TRUSS</span><span class="l2">SYSTEMS</span></span>
  <span class="tile-arrow"><svg width="20" height="24" viewBox="0 0 20 24"><path d="M5 2l10 10L5 22" stroke="#333" stroke-width="2.5" fill="none"/></svg></span>
</a>
<a class="abs tile" style="left:617px;top:896px;background:linear-gradient(135deg,#e0605a,#c8302c 55%,#8e1d1c)" role="img" aria-label="Stack of red speakers">
  <span class="tile-frame"></span>
  <span class="tile-label"><span class="l1">SOUND</span><span class="l2">SYSTEMS</span></span>
  <span class="tile-arrow"><svg width="20" height="24" viewBox="0 0 20 24"><path d="M5 2l10 10L5 22" stroke="#333" stroke-width="2.5" fill="none"/></svg></span>
</a>

<!-- featured products -->
<section class="abs" style="left:0;top:1117px;width:1200px;height:427px;background:var(--grey-bg)"></section>
<div class="abs section-bar" style="top:1139px;background:var(--pink)">
  <h2>FEATURED PRODUCTS</h2>
  <div class="pager"><i><svg width="10" height="12" viewBox="0 0 10 12"><path d="M7 1L2 6l5 5" stroke="#333" stroke-width="2" fill="none"/></svg></i><i><svg width="10" height="12" viewBox="0 0 10 12"><path d="M3 1l5 5-5 5" stroke="#333" stroke-width="2" fill="none"/></svg></i></div>
</div>

<div class="abs card" style="left:98px;top:1211px">
  <div class="card-media"><div class="shape" role="img" aria-label="Recessed LED canopy light" style="width:170px;height:110px;background:linear-gradient(160deg,#e4e4e4,#a8a8a8)"></div></div>
  <div class="card-title">Lorem ipsum</div><div class="card-text">Lorem ipsum dolor sit amet</div>
  <div class="card-btns"><span class="btn btn-pink">Buy Now</span><span class="btn btn-dark">On Rent</span></div>
</div>
<div class="abs card" style="left:352px;top:1211px">
  <div class="card-media"><div class="shape" role="img" aria-label="Moving head stage light" style="width:100px;height:140px;background:linear-gradient(180deg,#4a4a4a,#1d1d1d)"></div></div>
  <div class="card-title">Lorem ipsum</div><div class="card-text">Lorem ipsum dolor sit amet</div>
  <div class="card-btns"><span class="btn btn-pink">Buy Now</span><span class="btn btn-dark">On Rent</span></div>
</div>
<div class="abs card" style="left:606px;top:1211px">
  <div class="card-media"><div role="img" aria-label="Portable LED speaker" style="width:58px;height:140px;border-radius:24px;background:linear-gradient(180deg,#3a5fbf,#c0395b 55%,#1f2a6a)"></div></div>
  <div class="card-title">Lorem ipsum</div><div class="card-text">Lorem ipsum dolor sit amet</div>
  <div class="card-btns"><span class="btn btn-pink">Buy Now</span><span class="btn btn-dark">On Rent</span></div>
</div>
<div class="abs card" style="left:861px;top:1211px">
  <div class="card-media"><div class="shape" role="img" aria-label="Double sided LED billboard on a pole" style="width:180px;height:110px;background:linear-gradient(160deg,#2a2a2a,#0e0e0e)"></div></div>
  <div class="card-title">Lorem ipsum</div><div class="card-text">Lorem ipsum dolor sit amet</div>
  <div class="card-btns"><span class="btn btn-pink">Buy Now</span><span class="btn btn-dark">On Rent</span></div>
</div>

<!-- hot products -->
<section class="abs hot" role="img" aria-label="Teal tinted city skyline">
  <div class="abs hot-title">HOT PRODUCTS</div>
  <div class="abs hot-rule"></div>
  <div class="abs pager" style="left:1040px;top:48px"><i><svg width="10" height="12" viewBox="0 0 10 12"><path d="M7 1L2 6l5 5" stroke="#333" stroke-width="2" fill="none"/></svg></i><i><svg width="10" height="12" viewBox="0 0 10 12"><path d="M3 1l5 5-5 5" stroke="#333" stroke-width="2" fill="none"/></svg></i></div>
  <div class="abs hot-card" style="left:98px">
    <div class="hot-media" role="img" aria-label="Red lit speaker towers" style="background:linear-gradient(135deg,#2a0a0c,#8e1a1e 50%,#1a0606)"></div>
    <div class="hot-body"><h3>Lorem Ipsum Sed</h3><p>Lorem ipsum dolor sit amet, er adipiscing elit, sed diam nonrty erinibh euismod tincidunt reet do ewrererlore magna</p></div>
  </div>
  <div class="abs hot-card" style="left:611px">
    <div class="hot-media" role="img" aria-label="Colourful LED video screen" style="background:linear-gradient(135deg,#3a3a40,#5a8a3a 45%,#b23a2a 70%,#2a2a30)"></div>
    <div class="hot-body"><h3>Lorem Ipsum Sed</h3><p>Lorem ipsum dolor sit amet, er adipiscing elit, sed diam nonrty erinibh euismod tincidunt reet do ewrererlore magna</p></div>
  </div>
</section>

<!-- rental products -->
<div class="abs section-bar" style="top:1923px;background:var(--red)">
  <h2>RENTAL PRODUCTS</h2>
  <div class="pager"><i><svg width="10" height="12" viewBox="0 0 10 12"><path d="M7 1L2 6l5 5" stroke="#333" stroke-width="2" fill="none"/></svg></i><i><svg width="10" height="12" viewBox="0 0 10 12"><path d="M3 1l5 5-5 5" stroke="#333" stroke-width="2" fill="none"/></svg></i></div>
</div>

<div class="abs card" style="left:98px;top:1995px">
  <div class="card-media"><div class="shape" role="img" aria-label="LED street light head" style="width:170px;height:90px;background:linear-gradient(160deg,#d0d6de,#8d96a2)"></div></div>
  <div class="card-title">Lorem ipsum</div><div class="card-text">Lorem ipsum dolor sit amet</div>
  <div class="card-btns"><span class="btn btn-red">More Info</span><span class="btn btn-dark">Add to Cart</span></div>
</div>
<div class="abs card" style="left:352px;top:1995px">
  <div class="card-media"><div class="shape" role="img" aria-label="Aluminium truss frame" style="width:180px;height:130px;background:linear-gradient(180deg,#9a9a9a,#6a6a6a)"></div></div>
  <div class="card-title">Lorem ipsum</div><div class="card-text">Lorem ipsum dolor sit amet</div>
  <div class="card-btns"><span class="btn btn-red">More Info</span><span class="btn btn-dark">Add to Cart</span></div>
</div>
<div class="abs card" style="left:606px;top:1995px">
  <div class="card-media"><div class="shape" role="img" aria-label="Speaker set with green lights" style="width:180px;height:140px;background:linear-gradient(135deg,#1a1a1a,#1f7a3a 50%,#121212)"></div></div>
  <div class="card-title">Lorem ipsum</div><div class="card-text">Lorem ipsum dolor sit amet</div>
  <div class="card-btns"><span class="btn btn-red">More Info</span><span class="btn btn-dark">Add to Cart</span></div>
</div>
<div class="abs card" style="left:861px;top:1995px">
  <div class="card-media"><div class="shape" role="img" aria-label="Hanging LED high bay panel" style="width:140px;height:130px;background:linear-gradient(160deg,#e4e4e4,#9c9c9c)"></div></div>
  <div class="card-title">Lorem ipsum</div><div class="card-text">Lorem ipsum dolor sit amet</div>
  <div class="card-btns"><span class="btn btn-red">More Info</span><span class="btn btn-dark">Add to Cart</span></div>
</div>

<!-- features -->
<section class="abs features" role="img" aria-label="City skyline at night">
  <div class="abs feature" style="left:100px">
    <span class="feature-icon"><svg width="32" height="32" viewBox="0 0 32 32"><circle cx="16" cy="16" r="10" stroke="#111" stroke-width="5" stroke-dasharray="4 3" fill="none"/><circle cx="16" cy="16" r="4" fill="#111"/></svg></span>
    <h3>TECHNOLOGY</h3>
    <p>Lorem ipsum dolor sit amet, er adipiscing elit, sed diam nonrty erinibh euismo</p>
  </div>
  <div class="abs feature" style="left:443px">
    <span class="feature-icon"><svg width="32" height="32" viewBox="0 0 32 32"><circle cx="16" cy="16" r="13" stroke="#111" stroke-width="2.5" fill="none"/><path d="M9 16l5 5 9-10" stroke="#111" stroke-width="3.5" fill="none"/></svg></span>
    <h3>QUALITY</h3>
    <p>Lorem ipsum dolor sit amet, er adipiscing elit, sed diam nonrty erinibh euismo</p>
  </div>
  <div class="abs feature" style="left:784px">
    <span class="feature-icon"><svg width="32" height="32" viewBox="0 0 32 32"><rect x="4" y="14" width="6" height="14" fill="#111"/><path d="M12 14l6-10c3 0 3 3 2 6h7c2 0 3 2 2 4l-3 11c-1 2-2 3-4 3H12z" fill="#111"/></svg></span>
    <h3>WARRANTY</h3>
    <p>Lorem ipsum dolor sit amet, er adipiscing elit, sed diam nonrty erinibh euismo</p>
  </div>
</section>

<!-- newsletter -->
<section class="abs newsletter">
  <div class="abs nl-icon"><svg width="22" height="18" viewBox="0 0 22 18"><rect x="1" y="2" width="20" height="14" rx="1" fill="#fff"/><path d="M1 3l10 7 10-7" stroke="#e3302f" stroke-width="2" fill="none"/></svg></div>
  <div class="abs nl-label">Newsletter Signup</div>
  <div class="abs nl-input">Enter your email here</div>
  <div class="abs nl-btn">SUBSRIBE</div>
  <div class="abs follow">Follow Us On:&nbsp;<span class="social"></span><span class="social"></span><span class="social"></span><span class="social"></span></div>
</section>

<!-- footer -->
<footer class="abs footer">
  <div class="abs f-col" style="left:100px;top:24px;width:290px">
    <h4>About Us</h4>
    <p>Lorem ipsum dolor sit amet, consectetuer ere adipiscing elit, sed diam nonummy nibh smod tincidunt ut laoreet dolore magna aliquam rat volutpat. Ut wisi enim ad minim veniam.</p>
    <p style="margin-top:6px">Read More+</p>
  </div>
  <div class="abs f-divider" style="left:407px"></div>
  <div class="abs f-col" style="left:427px;top:24px">
    <h4>Quick Links</h4>
    <ul><li>Home</li><li>About Us</li><li>Products for Sale</li><li>Products for Rental</li><li>Contact Us</li></ul>
  </div>
  <div class="abs f-divider" style="left:598px"></div>
  <div class="abs f-col" style="left:637px;top:24px;width:240px">
    <h4>Contact Details</h4>
    <div class="contact-row"><svg width="14" height="18" viewBox="0 0 14 18"><path d="M7 17S1 10 1 6.5a6 6 0 0 1 12 0C13 10 7 17 7 17z" fill="#1e9c86"/><circle cx="7" cy="6.5" r="2.2" fill="#232323"/></svg><span>Lorem ipsum, Dollar smit,<br>city code - 1234567.</span></div>
    <div class="contact-row"><svg width="14" height="16" viewBox="0 0 14 16"><path d="M3 1l3 3-2 2c1 2 3 4 5 5l2-2 3 3-2 3C6 15 0 9 1 3z" fill="#1e9c86"/></svg><span>123-456-7890</span></div>
    <div class="contact-row"><svg width="14" height="12" viewBox="0 0 14 12"><rect x="0" y="1" width="14" height="10" fill="#1e9c86"/><path d="M0 1l7 5 7-5" stroke="#232323" stroke-width="1.4" fill="none"/></svg><span>inquiry@caldervaneled.com</span></div>
  </div>
  <div class="abs f-divider" style="left:876px"></div>
  <div class="abs f-col" style="left:906px;top:24px">
    <h4>We Accept</h4>
    <div class="cards"><b></b><b></b><b></b><b></b><b></b></div>
  </div>
  <div class="abs footer-brand"><span class="brand-dot" style="width:34px;height:34px"></span>CALDER VANE LED</div>
</footer>
<div class="abs copyright">COPYRIGHT © 2016 CALDER VANE LED. ALL RIGHTS RESERVED.</div>

</body>
</html>
```